Business card for medical clinic

I need an upmarket, modern medical/health business card for my clinic

Contact Information for Business Card

name, address, email, qr code

```html
<!DOCTYPE html>
<html lang="en">
<head>
<meta charset="utf-8">
<title>Meridia Care Clinic – Business Card</title>
<link href="https://fonts.googleapis.com/css2?family=Montserrat:wght@400;600;700&display=swap" rel="stylesheet">
<style>
  :root{
    --backdrop:#9a9a9a;
    --paper:#ffffff;
    --navy:#243b58;
    --steel:#2f6d93;
    --sky:#2f95c9;
    --ink:#1c1c1c;
    --icon:#2ea3db;
  }
  *{margin:0;padding:0;box-sizing:border-box}
  html,body{width:1093px;height:1200px;overflow:hidden}
  body{background:var(--backdrop);font-family:"Montserrat",sans-serif;position:relative;color:var(--ink)}
  .card{position:absolute;background:var(--paper);overflow:hidden}
  .card--front{left:264px;top:225px;width:581px;height:363px}
  .card--back{left:264px;top:616px;width:596px;height:366px}
  .card__band{position:absolute;left:0;right:0;bottom:0;height:15px;
    background:linear-gradient(90deg,var(--navy),var(--steel) 60%,var(--sky))}
  .brand{position:absolute;display:flex;align-items:center;color:var(--steel);font-weight:600;white-space:nowrap;line-height:1}
  .brand__dot{border:2px solid var(--steel);border-radius:50%;flex:none}
  .card--front .brand{left:80px;top:186px;height:28px;font-size:12px;gap:7px}
  .card--front .brand__dot{width:28px;height:28px}
  .card--back .brand{left:136px;top:153px;height:56px;font-size:21px;gap:12px}
  .card--back .brand__dot{width:56px;height:56px;border-width:3px}
  .divider{position:absolute;left:291px;top:111px;width:1.5px;height:171px;background:var(--icon)}
  .contact{position:absolute;left:306px;top:110px}
  .contact__name{font-size:21px;font-weight:700;color:var(--steel);line-height:1.2}
  .contact__role{font-size:13px;margin-top:2px}
  .contact__list{list-style:none;margin-top:20px}
  .contact__item{display:flex;align-items:center;gap:8px;font-size:13px;height:25.5px}
  .contact__item svg{width:13px;height:13px;flex:none;fill:var(--icon)}
  .contact__address{font-size:13px;line-height:16px;margin-top:11px}
</style>
</head>
<body>
  <section class="card card--front">
    <div class="brand"><span class="brand__dot"></span>MERIDIA CARE CLINIC</div>
    <div class="divider"></div>
    <div class="contact">
      <h1 class="contact__name">Daniel Harper</h1>
      <p class="contact__role">Managing Director</p>
      <ul class="contact__list">
        <li class="contact__item">
          <svg viewBox="0 0 24 24"><path d="M6.6 10.8a15 15 0 0 0 6.6 6.6l2.2-2.2c.3-.3.7-.4 1-.2 1.1.4 2.3.6 3.6.6.6 0 1 .4 1 1V20c0 .6-.4 1-1 1A17 17 0 0 1 3 4c0-.6.4-1 1-1h3.5c.6 0 1 .4 1 1 0 1.3.2 2.5.6 3.6.1.3 0 .7-.2 1z"/></svg>
          555.014.2290
        </li>
        <li class="contact__item">
          <svg viewBox="0 0 24 24"><path d="M3 5h18c.6 0 1 .4 1 1v.4l-10 6.3L2 6.4V6c0-.6.4-1 1-1zm-1 3.7l10 6.3 10-6.3V18c0 .6-.4 1-1 1H3c-.6 0-1-.4-1-1z"/></svg>
          info@meridiacare.com
        </li>
        <li class="contact__item">
          <svg viewBox="0 0 24 24"><circle cx="12" cy="12" r="10"/></svg>
          www.meridiacare.com
        </li>
      </ul>
      <p class="contact__address">240 Cedar Hollow Lane<br>Fairview, MS 39012</p>
    </div>
    <div class="card__band"></div>
  </section>

  <section class="card card--back">
    <div class="brand"><span class="brand__dot"></span>MERIDIA CARE CLINIC</div>
    <div class="card__band"></div>
  </section>
</body>
</html>
```